Translational academic medical clinical group needs website redesign

We have a very rudimentary website that needs a redesign and to be made mobile friendly. We are just finished a logo project and will have a new logo to start the redesign this week. Our current website is k7m4.org. We need a place to profile each researcher in our group, display our publications and have a place to describe current and past projects. It needs to be mobile friendly, have a QRS code that we can print on presentations and posters. It would be nice to have our publications automatically upload from paper orchard but we would at least link each researcher to their paper orchard profile.

Research community and dissemination of published research

• A profile page for each researcher, a place to link to current publications and paper orchard for each researcher, a place to describe current projects. It needs to be mobile friendly.
• It would be fantastic if the publication links can be automatically generated from paper orchard.
• Open to any suggestions. Avoid pink/purple colours. We are academic and clinical research so University and hospital.

```html
<!DOCTYPE html>
<html lang="en">
<head>
<meta charset="utf-8">
<title>Critical Care Lab-to-Ward Research Group</title>
<link rel="stylesheet" href="https://fonts.googleapis.com/css2?family=Rubik:wght@400;500;700&family=Open+Sans:wght@400;600&display=swap">
<style>
:root{
  --brand:#0c33a3;
  --brand-light:#6f9be0;
  --ink:#1b1b1b;
  --ink-soft:#444;
  --mist:#f4f1f1;
  --line:#c9c6c6;
  --white:#fff;
}
*{margin:0;padding:0;box-sizing:border-box}
html,body{width:1200px;height:2999px;overflow:hidden}
body{position:relative;background:var(--white);font-family:'Open Sans',sans-serif;color:var(--ink)}
.abs{position:absolute}
.btn{position:absolute;background:var(--brand);color:var(--white);font-family:'Rubik',sans-serif;font-weight:500;display:flex;align-items:center;justify-content:center;letter-spacing:.3px}
.bar{position:absolute;height:3px;background:var(--brand)}

/* header */
.site-header{left:0;top:0;width:1200px;height:119px;background:var(--brand)}
.brand-mark{left:136px;top:16px;width:150px;height:90px;color:var(--white);font-family:'Rubik',sans-serif;text-align:center}
.brand-mark .dot{width:40px;height:40px;border-radius:50%;background:var(--brand-light);margin:0 auto 6px}
.brand-mark .name{font-size:13px;font-weight:500;letter-spacing:.5px}
.brand-mark .sub{font-size:9px;letter-spacing:4px;margin-top:3px}
.follow-label{left:705px;top:34px;color:var(--white);font:500 12px 'Rubik',sans-serif}
.social-dot{top:30px;width:25px;height:25px;border-radius:50%}
.search{left:884px;top:25px;width:185px;height:33px;background:var(--white);font:400 11px 'Rubik',sans-serif;padding:11px 13px;color:#222}
.search svg{position:absolute;right:10px;top:11px}
.nav{top:84px;color:var(--white);font:500 14px 'Rubik',sans-serif;letter-spacing:.3px}

/* hero */
.hero{left:0;top:119px;width:1200px;height:510px;background:linear-gradient(110deg,#cfe0f3 0%,#6f94c9 30%,#2a58a6 60%,#173f8c 100%)}
.hero-title{left:134px;font:700 44px/58px 'Rubik',sans-serif;color:var(--brand);background:rgba(255,255,255,.82);padding:0 10px;letter-spacing:.5px}
.hero-dots{left:560px;top:586px;display:flex;gap:9px;align-items:center}
.hero-dots span{width:7px;height:7px;border-radius:50%;background:var(--white)}
.hero-dots span.on{width:11px;height:11px;border:2px solid var(--white);background:var(--brand)}

/* welcome */
.welcome-photo{left:133px;top:677px;width:455px;height:332px;background:linear-gradient(135deg,#8a8a8a,#4c4c4c 55%,#2f2f2f)}
.welcome-kicker{left:630px;top:671px;font:400 20px 'Rubik',sans-serif}
.welcome-title{left:630px;top:697px;font:700 24px/32px 'Rubik',sans-serif;letter-spacing:.3px}
.welcome-text{left:630px;top:806px;width:450px;font:400 18px/26.5px 'Open Sans',sans-serif;color:var(--ink)}

/* blog */
.blog{left:0;top:1057px;width:1200px;height:538px;background:var(--mist)}
.section-title{width:1200px;left:0;text-align:center;font:500 24px 'Rubik',sans-serif;letter-spacing:.3px}
.blog-card{top:1168px;width:298px;height:380px;background:var(--white);border:1px solid var(--line)}
.blog-card .pic{height:197px}
.blog-card h3{position:absolute;left:23px;top:218px;width:240px;font:500 14.5px/19px 'Rubik',sans-serif;letter-spacing:.2px}
.blog-card p{position:absolute;left:23px;top:263px;width:232px;font:400 12.5px/17px 'Open Sans',sans-serif;color:var(--ink-soft)}
.blog-card .btn{left:23px;top:329px;width:91px;height:25px;font-size:11.5px}

/* researchers */
.person{top:1711px;width:224px;height:386px;background:var(--white);border:1px solid var(--line)}
.person .pic{height:196px}
.person h3{position:absolute;left:17px;top:213px;font:500 12.5px 'Rubik',sans-serif;letter-spacing:.2px}
.person p{position:absolute;left:17px;top:240px;width:190px;font:400 11.5px/16px 'Open Sans',sans-serif;color:var(--ink-soft)}
.person .btn{left:17px;top:336px;width:79px;height:24px;font-size:11px}
.arrow{top:1893px}

/* presentations */
.pubs{left:0;top:2148px;width:585px;height:483px;background:var(--mist)}
.pubs-photo{left:585px;top:2148px;width:615px;height:483px;background:radial-gradient(circle at 45% 45%,#e9e4dc,#b9c4cf 45%,#8ea4bd 100%)}
.pubs-title{left:134px;top:2189px;font:700 25px/32px 'Rubik',sans-serif;letter-spacing:.3px}
.pub-title{left:134px;font:400 16px/22px 'Rubik',sans-serif}
.pub-meta{left:134px;width:420px;font:400 12px/16px 'Open Sans',sans-serif;color:var(--ink-soft)}
.pub-rule{left:134px;top:2422px;width:411px;height:1px;background:#bdb8b8}

/* footer */
.site-footer{left:0;top:2631px;width:1200px;height:368px;background:var(--brand)}
.foot-brand{left:134px;top:2680px;width:210px;color:var(--white);text-align:center;font-family:'Rubik',sans-serif}
.foot-brand .dot{width:56px;height:56px;border-radius:50%;background:var(--brand-light);margin:0 auto 14px}
.foot-brand .name{font-size:16px;font-weight:500;letter-spacing:.6px}
.foot-brand .sub{font-size:11px;letter-spacing:6px;margin-top:4px}
.foot-head{top:2673px;color:var(--white);font:500 13px 'Rubik',sans-serif;letter-spacing:.4px}
.foot-menu{left:436px;top:2713px;color:var(--white);font:400 11.5px/20px 'Rubik',sans-serif}
.foot-item{color:var(--white);font:400 11.5px/15px 'Rubik',sans-serif}
.icon-circle{width:22px;height:22px;border-radius:50%;background:var(--white);display:flex;align-items:center;justify-content:center}
.foot-rule{left:134px;top:2889px;width:935px;height:1px;background:rgba(255,255,255,.3)}
.copyright{left:136px;top:2935px;color:var(--white);font:400 12px 'Rubik',sans-serif}
.badge-a{left:875px;top:2921px;width:105px;height:54px;background:#a6192e}
.badge-b{left:1013px;top:2918px;width:56px;height:56px;border-radius:50%;background:var(--white)}
</style>
</head>
<body>

<header class="abs site-header">
  <div class="abs brand-mark">
    <div class="dot"></div>
    <div class="name">K7M4 CRITICAL CARE</div>
    <div class="sub">LAB TO WARD</div>
  </div>
  <div class="abs follow-label">FOLLOW US</div>
  <div class="abs social-dot" style="left:795px;background:#2c54b8"></div>
  <div class="abs social-dot" style="left:829px;background:#1da1f2"></div>
  <div class="abs search">SEARCH
    <svg width="11" height="11" viewBox="0 0 12 12"><circle cx="5" cy="5" r="3.8" fill="none" stroke="#888" stroke-width="1.4"/><line x1="8" y1="8" x2="11" y2="11" stroke="#888" stroke-width="1.4"/></svg>
  </div>
  <nav>
    <div class="abs nav" style="left:557px">HOME</div>
    <div class="abs nav" style="left:639px">ABOUT US</div>
    <div class="abs nav" style="left:750px">PRESENTATIONS &amp; PUBLICATIONS</div>
    <div class="abs nav" style="left:1027px">MORE</div>
  </nav>
</header>

<section class="abs hero" role="img" aria-label="Researcher in lab coat and safety glasses holding a test tube in a laboratory"></section>
<div class="abs hero-title" style="top:262px">LAB-TO-WARD</div>
<div class="abs hero-title" style="top:323px">RESEARCH GROUP</div>
<div class="btn" style="left:134px;top:387px;width:126px;height:36px;font-size:16px">READ MORE</div>
<div class="abs hero-dots"><span></span><span></span><span class="on"></span><span></span><span></span></div>

<div class="abs welcome-photo" role="img" aria-label="Group of researchers presenting a large donation cheque beside a hospital stretcher"></div>
<div class="abs welcome-kicker">WELCOME TO THE</div>
<h1 class="abs welcome-title">CRITICAL CARE LAB-TO-WARD<br>RESEARCH GROUP WEBSITE.</h1>
<div class="bar" style="left:630px;top:771px;width:115px"></div>
<p class="abs welcome-text">We are a multi-disciplinary group of clinician - researchers who are passionate about studying novel medical technologies aimed at improving outcomes for critically ill patients. Take a look around to learn more about our research!</p>
<div class="btn" style="left:630px;top:970px;width:103px;height:31px;font-size:13px">READ MORE</div>

<section class="abs blog"></section>
<h2 class="abs section-title" style="top:1090px">LATEST BLOG</h2>
<div class="bar" style="left:580px;top:1131px;width:39px"></div>

<article class="abs blog-card" style="left:134px">
  <div class="pic" role="img" aria-label="Gloved hand holding a flask of blue liquid beside beakers" style="background:linear-gradient(135deg,#d9e9f6,#5ea6e0 55%,#1f67b4)"></div>
  <h3>LOREM IPSUM IS SIMPLY DUMMY TEXT OF THE PRINTING</h3>
  <p>It is a long established fact that a reader will be distracted by the readable content of a page</p>
  <div class="btn">READ MORE</div>
</article>
<article class="abs blog-card" style="left:452px">
  <div class="pic" role="img" aria-label="Close-up of a laboratory microscope with a slide" style="background:linear-gradient(135deg,#6fa2d8,#2a64b3 55%,#10346f)"></div>
  <h3>LOREM IPSUM IS SIMPLY DUMMY TEXT OF THE PRINTING</h3>
  <p>It is a long established fact that a reader will be distracted by the readable content of a page</p>
  <div class="btn">READ MORE</div>
</article>
<article class="abs blog-card" style="left:771px">
  <div class="pic" role="img" aria-label="Researcher in surgical cap and mask working with lab equipment" style="background:linear-gradient(135deg,#aebccd,#5e7894 55%,#2c3e55)"></div>
  <h3>LOREM IPSUM IS SIMPLY DUMMY TEXT OF THE PRINTING</h3>
  <p>It is a long established fact that a reader will be distracted by the readable content of a page</p>
  <div class="btn">READ MORE</div>
</article>

<h2 class="abs section-title" style="top:1630px">RESEARCHER</h2>
<div class="bar" style="left:580px;top:1673px;width:39px"></div>

<svg class="abs arrow" style="left:78px" width="18" height="28" viewBox="0 0 18 28"><polyline points="14,3 4,14 14,25" fill="none" stroke="#999" stroke-width="2"/></svg>
<svg class="abs arrow" style="left:1096px" width="18" height="28" viewBox="0 0 18 28"><polyline points="4,3 14,14 4,25" fill="none" stroke="#999" stroke-width="2"/></svg>

<article class="abs person" style="left:134px">
  <div class="pic" role="img" aria-label="Portrait of Dr. Marcus Hale in a white coat" style="background:linear-gradient(135deg,#e8ebee,#b7c2cc)"></div>
  <h3>DR. MARCUS HALE</h3>
  <p>Dr. Hale is a researcher and critical care physician at the Harbourview General Hospital. He is the recipient of the Harbourview General Hospital</p>
  <div class="btn">VIEW BIO</div>
</article>
<article class="abs person" style="left:371px">
  <div class="pic" role="img" aria-label="Portrait of Ingrid Vossberg" style="background:linear-gradient(135deg,#d9dde3,#a9b1ba)"></div>
  <h3>INGRID VOSSBERG</h3>
  <p>Ingrid Vossberg is PhD candidate at Northgate University (NGU) interested in studying the effects of long-term mechanical ventilation on lung structure and function.</p>
  <div class="btn">VIEW BIO</div>
</article>
<article class="abs person" style="left:608px">
  <div class="pic" role="img" aria-label="Portrait of Tomas Ridley outdoors" style="background:linear-gradient(135deg,#8f8578,#5d5347)"></div>
  <h3>TOMAS RIDLEY</h3>
  <p>Tomas Ridley has returned to Northgate University (NGU) as PhD candidate studying the effects of long-term mechanical ventilation on diaphragm</p>
  <div class="btn">VIEW BIO</div>
</article>
<article class="abs person" style="left:845px">
  <div class="pic" role="img" aria-label="Portrait of Dr. Aurelio Minardi" style="background:linear-gradient(135deg,#f0f0f0,#c7ccd3)"></div>
  <h3>DR. AURELIO MINARDI</h3>
  <p>Dr. Aurelio Minardi is PhD candidate at Northgate University (NGU) interested in studying the effects of long-term mechanical ventilation on the nervous system.</p>
  <div class="btn">VIEW BIO</div>
</article>

<section class="abs pubs"></section>
<div class="abs pubs-photo" role="img" aria-label="Researcher looking into a microscope in a bright laboratory"></div>
<h2 class="abs pubs-title">RECENT PRESENTATIONS &amp;<br>PUBLICATIONS</h2>
<div class="bar" style="left:134px;top:2261px;width:39px"></div>

<div class="abs pub-title" style="top:2297px;width:350px">Negative Hippocampal Turnover Index After 50 Hours of Gold-Standard Mechanical Ventilation in a Pre-Clinical Pig Model</div>
<div class="abs pub-meta" style="top:2370px">DOI: 10.4402/cclw-conference.2020.118.2_MeetingAbstracts.<br>B3107 Conference: NRS 2020</div>
<div class="abs pub-rule"></div>
<div class="abs pub-title" style="top:2440px;width:420px">Better PAO2/FIO2 with Temporary Transvenous Neurostimulation Versus Mechanical Ventilation Alone</div>
<div class="abs pub-meta" style="top:2490px">DOI:&nbsp; 10.2261/02.ccr.0000517723.40866.12<br>Critical Care Reviews 31:407</div>
<div class="btn" style="left:138px;top:2549px;width:102px;height:31px;font-size:13px">READ MORE</div>

<footer class="abs site-footer"></footer>
<div class="abs foot-brand">
  <div class="dot"></div>
  <div class="name">K7M4 CRITICAL CARE</div>
  <div class="sub">LAB TO WARD</div>
</div>

<div class="abs foot-head" style="left:436px">MENU</div>
<div class="abs foot-menu">HOME<br>ABOUT<br>FIRE SERVICES PLANS<br>FIRE BLOCK PLANS<br>CONTACT US</div>

<div class="abs foot-head" style="left:653px">CONTACT US</div>
<div class="abs icon-circle" style="left:651px;top:2736px">
  <svg width="10" height="12" viewBox="0 0 10 12"><path d="M5 0a4 4 0 0 0-4 4c0 3 4 8 4 8s4-5 4-8a4 4 0 0 0-4-4z" fill="#0c33a3"/><circle cx="5" cy="4" r="1.4" fill="#fff"/></svg>
</div>
<div class="abs foot-item" style="left:684px;top:2733px">Room 4120, Northgate University<br>1400 College Ave, Eastbay, BC V0X 2R7</div>
<div class="abs icon-circle" style="left:651px;top:2786px">
  <svg width="11" height="11" viewBox="0 0 12 12"><path d="M2.5 1l2 2.2-1.2 1.5a7 7 0 0 0 4 4l1.5-1.2L11 9.5 9.6 11C5 11 1 7 1 2.4z" fill="#0c33a3"/></svg>
</div>
<div class="abs foot-item" style="left:684px;top:2783px">Call Us<br>+614 55 019 442</div>
<div class="abs icon-circle" style="left:651px;top:2836px">
  <svg width="11" height="9" viewBox="0 0 12 9"><rect x="0.5" y="0.5" width="11" height="8" fill="#0c33a3"/><polyline points="0.5,0.5 6,5 11.5,0.5" fill="none" stroke="#fff" stroke-width="1"/></svg>
</div>
<div class="abs foot-item" style="left:684px;top:2833px">E mail Us<br>info@k7m4.org</div>

<div class="abs foot-head" style="left:964px">FOLLOW US</div>
<div class="abs icon-circle" style="left:964px;top:2736px"></div>
<div class="abs foot-item" style="left:998px;top:2733px">Like us on<br>FOLKPAGE</div>
<div class="abs icon-circle" style="left:964px;top:2786px"></div>
<div class="abs foot-item" style="left:998px;top:2783px">Follow us on<br>CHIRPLINE</div>
<div class="abs icon-circle" style="left:964px;top:2836px"></div>
<div class="abs foot-item" style="left:998px;top:2833px">Follow us on<br>WORKLINK</div>

<div class="abs foot-rule"></div>
<div class="abs copyright">Copyright © 2021 All Rights Reserved</div>
<div class="abs badge-a"></div>
<div class="abs badge-b"></div>

</body>
</html>
```